Brisk Hound Signage

This design is for "signage" that we intend to get produced.
A couple of different designs that say "Brisk Hound on Guard" and "Beware of Brisk Hound"
It should also have our logo (BH) plus our logo with the hand and dog paw. We would also like the main picture of the sign to be the attached. We would like a classy sophisticated look similar to our logo you designed.
Our designs will go on consumers gates/entrances to warn people there is a dog on the premises. I will get a better quality picture of the dog.

```html
<!DOCTYPE html>
<html lang="en">
<head>
<meta charset="utf-8">
<title>Brisk Hound Signage</title>
<link href="https://fonts.googleapis.com/css2?family=Great+Vibes&display=swap" rel="stylesheet">
<style>
  :root {
    --backdrop: #5e5e5e;
    --sign: #ffffff;
    --ink: #231f20;
    --dog-tone: #3d3d3d;
  }
  html, body {
    margin: 0;
    width: 1200px;
    height: 1200px;
    overflow: hidden;
    background: var(--backdrop);
  }
  .board { display: block; width: 1200px; height: 1200px; }
  .sign-face { fill: var(--sign); }
  .frame-line { fill: none; stroke: var(--ink); stroke-width: 4; }
  .frame-loop { fill: var(--sign); stroke: var(--ink); stroke-width: 4; }
  .half-disc { fill: var(--ink); }
  .dog-art { fill: var(--dog-tone); stroke: var(--sign); stroke-width: 4; }
  .name-band { fill: var(--ink); stroke: var(--sign); stroke-width: 2; }
  .name-dot { fill: var(--sign); stroke: var(--ink); stroke-width: 3; }
  .name-text {
    font-family: "Great Vibes", cursive;
    fill: var(--sign);
    text-anchor: middle;
  }
  .sign-words {
    font-family: "Great Vibes", cursive;
    fill: var(--ink);
    text-anchor: middle;
  }
</style>
</head>
<body>
<svg class="board" viewBox="0 0 1932 1932" xmlns="http://www.w3.org/2000/svg">

  <!-- Round sign: on guard -->
  <g class="sign sign-round sign-on-guard">
    <circle class="sign-face" cx="574" cy="660" r="296"/>
    <circle class="frame-line" cx="574" cy="660" r="272"/>
    <circle class="frame-loop" cx="394" cy="482" r="11"/>
    <circle class="frame-loop" cx="754" cy="482" r="11"/>
    <circle class="frame-loop" cx="394" cy="838" r="11"/>
    <circle class="frame-loop" cx="754" cy="838" r="11"/>
    <path class="half-disc" d="M411 660 A163 163 0 0 1 737 660 Z"/>
    <rect class="dog-art" x="488" y="452" width="170" height="210" rx="30" role="img" aria-label="Low-poly illustration of a seated dog"/>
    <rect class="name-band" x="373" y="677" width="402" height="73" rx="36"/>
    <circle class="name-dot" cx="409" cy="713" r="30"/>
    <text class="name-text" x="580" y="728" font-size="52">Brisk Hound</text>
    <text class="sign-words" x="574" y="830" font-size="78">On Guard</text>
  </g>

  <!-- Round sign: beware of -->
  <g class="sign sign-round sign-beware">
    <circle class="sign-face" cx="1358" cy="660" r="296"/>
    <circle class="frame-line" cx="1358" cy="660" r="272"/>
    <circle class="frame-loop" cx="1178" cy="482" r="11"/>
    <circle class="frame-loop" cx="1538" cy="482" r="11"/>
    <circle class="frame-loop" cx="1178" cy="838" r="11"/>
    <circle class="frame-loop" cx="1538" cy="838" r="11"/>
    <path class="half-disc" d="M1195 660 A163 163 0 0 1 1521 660 Z"/>
    <rect class="dog-art" x="1272" y="452" width="170" height="210" rx="30" role="img" aria-label="Low-poly illustration of a seated dog"/>
    <text class="sign-words" x="1355" y="745" font-size="92">Beware Of</text>
    <rect class="name-band" x="1196" y="773" width="324" height="60" rx="30"/>
    <circle class="name-dot" cx="1227" cy="803" r="24"/>
    <text class="name-text" x="1372" y="817" font-size="42">Brisk Hound</text>
  </g>

  <!-- Rectangular sign: on guard -->
  <g class="sign sign-rect sign-on-guard">
    <rect class="sign-face" x="191" y="976" width="765" height="590"/>
    <rect class="frame-line" x="215" y="999" width="717" height="544" rx="20"/>
    <circle class="frame-loop" cx="250" cy="1035" r="13"/>
    <circle class="frame-loop" cx="897" cy="1035" r="13"/>
    <circle class="frame-loop" cx="250" cy="1508" r="13"/>
    <circle class="frame-loop" cx="897" cy="1508" r="13"/>
    <path class="half-disc" d="M378 1291 A196 196 0 0 1 770 1291 Z"/>
    <rect class="dog-art" x="470" y="1040" width="205" height="254" rx="34" role="img" aria-label="Low-poly illustration of a seated dog"/>
    <rect class="name-band" x="333" y="1305" width="480" height="90" rx="45"/>
    <circle class="name-dot" cx="377" cy="1350" r="36"/>
    <text class="name-text" x="588" y="1369" font-size="64">Brisk Hound</text>
    <text class="sign-words" x="570" y="1480" font-size="95">On Guard</text>
  </g>

  <!-- Rectangular sign: beware of -->
  <g class="sign sign-rect sign-beware">
    <rect class="sign-face" x="976" y="976" width="765" height="590"/>
    <rect class="frame-line" x="1000" y="999" width="717" height="544" rx="20"/>
    <circle class="frame-loop" cx="1035" cy="1035" r="13"/>
    <circle class="frame-loop" cx="1682" cy="1035" r="13"/>
    <circle class="frame-loop" cx="1035" cy="1508" r="13"/>
    <circle class="frame-loop" cx="1682" cy="1508" r="13"/>
    <path class="half-disc" d="M1162 1291 A196 196 0 0 1 1554 1291 Z"/>
    <rect class="dog-art" x="1254" y="1040" width="205" height="254" rx="34" role="img" aria-label="Low-poly illustration of a seated dog"/>
    <text class="sign-words" x="1355" y="1370" font-size="100">Beware Of</text>
    <rect class="name-band" x="1134" y="1417" width="448" height="85" rx="42"/>
    <circle class="name-dot" cx="1177" cy="1459" r="34"/>
    <text class="name-text" x="1372" y="1478" font-size="58">Brisk Hound</text>
  </g>

</svg>
</body>
</html>
```